Whiskey label design and bottle design

We need a label design for our new whiskey company. We are going to use paper logo that can include any elements that the designer wants including shinny, glossy, etc. We need something eye catching that stands out. Our bottle has not been chosen so we are can use any type of bottle including a custom bottle. Something that looks expensive. High quality. Need to stand out. The Brand name for now is the Heart of Ashmere

Target Market(s)

21 to 54 60% male, 40% female

Industry/Entity Type

Whiskey Spirits

Requirements
Must have
• Detailed packaging, A barcode for the SKU, Governement warning on the back, Area for a story on the back, size of bottle on the back, Cork Closure.
Nice to have
• Something with tradition, Quality, and it stands out from comeptors. High quality labels.

```html
<!DOCTYPE html>
<html lang="en">
<head>
<meta charset="utf-8">
<title>Heart of Ashmere — Whiskey Label</title>
<link rel="stylesheet" href="https://fonts.googleapis.com/css2?family=Alegreya:wght@400;700;800&family=Alegreya+SC:wght@400;700&display=swap">
<style>
  :root {
    --label-black: #0e0e0e;
    --gold: #c9a14a;
    --gold-deep: #a8823a;
    --white: #ffffff;
    --ribbon: #3a3838;
    --page: #f3f3f3;
    --band: #050505;
    --muted: #4a4a4a;
  }
  * { margin: 0; padding: 0; box-sizing: border-box; }
  html, body { width: 1200px; height: 1200px; overflow: hidden; }
  body {
    background: radial-gradient(ellipse at 50% 40%, #ffffff 0%, var(--page) 70%, #e9e9e9 100%);
    font-family: "Alegreya", Georgia, serif;
    position: relative;
  }
  .label-stage { position: absolute; left: 0; top: 0; width: 1200px; height: 768px; }
  .label-stage svg { display: block; width: 1200px; height: 768px; }
  .serif { font-family: "Alegreya", Georgia, serif; }
  .caps { font-family: "Alegreya SC", Georgia, serif; }
  .brand-band {
    position: absolute; left: 0; top: 768px; width: 1200px; height: 432px;
    background: var(--band);
  }
  .brand-band .state-outline {
    position: absolute; left: 575px; top: 60px; width: 590px; height: 270px;
    background: linear-gradient(180deg, rgba(80,80,80,0.35), rgba(60,60,60,0.2));
    border-radius: 6px;
  }
  .brand-band .wordmark {
    position: absolute; left: 575px; top: 60px; width: 590px; height: 270px;
    display: flex; align-items: center; justify-content: center;
    text-align: center; color: var(--gold);
    font-family: "Alegreya", Georgia, serif; font-weight: 800;
    font-size: 92px; line-height: 1.05;
  }
</style>
</head>
<body>

<section class="label-stage">
  <svg viewBox="0 0 1932 1237" xmlns="http://www.w3.org/2000/svg">
    <!-- die-cut label body -->
    <polygon class="label-body" fill="var(--label-black)"
      points="700,185 1232,185 1250,203 1250,300 1380,300 1395,315 1395,955 1380,970 1250,970 1250,1072 1232,1090 700,1090 682,1072 682,970 552,970 537,955 537,315 552,300 682,300 682,203"/>

    <!-- side panel frames -->
    <rect x="553" y="322" width="115" height="625" fill="none" stroke="var(--white)" stroke-width="2"/>
    <rect x="562" y="332" width="97" height="605" fill="none" stroke="var(--white)" stroke-width="1"/>
    <rect x="1264" y="322" width="115" height="625" fill="none" stroke="var(--white)" stroke-width="2"/>
    <rect x="1273" y="332" width="97" height="605" fill="none" stroke="var(--white)" stroke-width="1"/>

    <!-- front panel frames -->
    <rect x="720" y="230" width="492" height="818" fill="none" stroke="var(--white)" stroke-width="3"/>
    <rect x="745" y="252" width="442" height="774" fill="none" stroke="var(--gold)" stroke-width="3"/>
    <line x1="770" y1="240" x2="1162" y2="240" stroke="var(--white)" stroke-width="2" stroke-dasharray="3 4"/>
    <line x1="770" y1="1038" x2="1162" y2="1038" stroke="var(--white)" stroke-width="2" stroke-dasharray="3 4"/>

    <!-- established plate -->
    <path d="M860,295 Q860,255 900,255 L1030,255 Q1070,255 1070,295 Z" fill="none" stroke="var(--gold)" stroke-width="4"/>
    <text class="caps" x="965" y="288" text-anchor="middle" font-size="34" fill="var(--gold)" letter-spacing="2">EST. 2022</text>

    <!-- age badge and type -->
    <circle cx="840" cy="360" r="45" fill="none" stroke="var(--white)" stroke-width="3"/>
    <circle cx="840" cy="360" r="37" fill="none" stroke="var(--gold)" stroke-width="2"/>
    <text class="serif" x="840" y="380" text-anchor="middle" font-size="56" fill="var(--gold)">12</text>
    <text class="caps" x="900" y="373" font-size="46" fill="var(--gold)" letter-spacing="5">Whiskey</text>
    <line x1="885" y1="385" x2="1150" y2="385" stroke="var(--white)" stroke-width="2"/>
    <line x1="885" y1="338" x2="1150" y2="338" stroke="var(--white)" stroke-width="2"/>

    <!-- state outline area -->
    <rect x="905" y="405" width="120" height="48" fill="#2a2a2a" rx="4" role="img" aria-label="Outline of the home state with radiating light rays"/>

    <!-- name banner -->
    <g class="name-banner">
      <polygon points="690,548 1240,410 1240,725 690,860" fill="var(--label-black)" stroke="var(--gold)" stroke-width="3"/>
      <polygon points="705,560 1225,428 1225,712 705,845" fill="none" stroke="var(--white)" stroke-width="2"/>
      <polygon points="716,570 1214,442 1214,700 716,832" fill="none" stroke="var(--white)" stroke-width="1" stroke-dasharray="2 4"/>
      <text class="serif" x="965" y="630" text-anchor="middle" font-size="104" font-weight="800" fill="var(--gold)">Heart of</text>
      <text class="serif" x="965" y="740" text-anchor="middle" font-size="104" font-weight="800" fill="var(--gold)">Ashmere</text>
    </g>

    <!-- distillery pill -->
    <rect x="820" y="848" width="305" height="38" rx="19" fill="none" stroke="var(--gold)" stroke-width="3"/>
    <text class="serif" x="972" y="878" text-anchor="middle" font-size="29" fill="var(--white)" letter-spacing="1.5">BEST DISTILLERY</text>

    <!-- volume -->
    <text class="caps" x="970" y="940" text-anchor="middle" font-size="24" fill="var(--gold)">Vol.750 ml</text>

    <!-- quality ribbon -->
    <path d="M825,930 Q970,1060 1120,930 L1120,965 Q970,1095 825,965 Z" fill="var(--ribbon)" stroke="var(--white)" stroke-width="2"/>
    <path id="ribbon-path" d="M845,958 Q970,1062 1100,958" fill="none"/>
    <text class="serif" font-size="28" fill="var(--gold)" letter-spacing="2">
      <textPath href="#ribbon-path" startOffset="50%" text-anchor="middle">HIGH QUALITY</textPath>
    </text>

    <!-- left story panel -->
    <g class="story-left" transform="translate(610,635) rotate(90)" font-size="12" fill="var(--white)" text-anchor="middle">
      <text class="serif" x="0" y="-35">Born of patient hands and limestone water, this whiskey rests for twelve long years in</text>
      <text class="serif" x="0" y="-22">charred oak barrels within our old rickhouse. Summers draw the spirit deep into the wood,</text>
      <text class="serif" x="0" y="-9">winters return it richer, and each season leaves its mark of caramel, vanilla and spice.</text>
      <text class="serif" x="0" y="4">We mill local grain, ferment in small batches and distil slowly in copper stills,</text>
      <text class="serif" x="0" y="17">bottling every cask by hand so that nothing is rushed and nothing is lost along</text>
      <text class="serif" x="0" y="30">the way. Pour a measure, let it breathe, and share it with friends who appreciate</text>
      <text class="serif" x="0" y="43">honest craft, quiet tradition and a long, warm finish worth waiting for.</text>
    </g>

    <!-- right story panel -->
    <g class="story-right" transform="translate(1321,635) rotate(-90)" font-size="12" fill="var(--white)" text-anchor="middle">
      <text class="serif" x="0" y="-35">Born of patient hands and limestone water, this whiskey rests for twelve long years in</text>
      <text class="serif" x="0" y="-22">charred oak barrels within our old rickhouse. Summers draw the spirit deep into the wood,</text>
      <text class="serif" x="0" y="-9">winters return it richer, and each season leaves its mark of caramel, vanilla and spice.</text>
      <text class="serif" x="0" y="4">We mill local grain, ferment in small batches and distil slowly in copper stills,</text>
      <text class="serif" x="0" y="17">bottling every cask by hand so that nothing is rushed and nothing is lost along</text>
      <text class="serif" x="0" y="30">the way. Pour a measure, let it breathe, and share it with friends who appreciate</text>
      <text class="serif" x="0" y="43">honest craft, quiet tradition and a long, warm finish worth waiting for.</text>
    </g>
  </svg>
</section>

<section class="brand-band">
  <div class="state-outline" role="img" aria-label="Faint outline of the home state behind the brand name"></div>
  <div class="wordmark">Heart of<br>Ashmere</div>
</section>

</body>
</html>
```